Food humor T-shirt and apparel company needs a Shopify site designed. We have logo files to help.

We are an apparel company based in Chicago by two cooking and food humor enthusiasts. We are looking for a redesign of our Shopify site. Our products are humorous quotes and pictures on shirts, sweaters and other apparel. The tagline for the company is - Find Your Yum. Wear Your Food. We want to see designs that incorporate our logo, brand color of royal purple, signify fun business casual clothing with amusing tags or images of trendy or esoteric food trends. The design should communicate excellence in taste but with maybe a satirical almost corporate type spin.
Target Market(s)
Hip, millennial foodies and cooks that love to try new foods, have great taste, and love to experiment in the restaurant or the kitchen.
Industry/Entity Type
Cooking
Look and feel
Each slider illustrates characteristics of the customer's brand and the style your logo design should communicate.

```html
<!DOCTYPE html>
<html lang="en">
<head>
<meta charset="utf-8">
<title>Forkora — Find Your Yum. Wear Your Food.</title>
<link href="https://fonts.googleapis.com/css2?family=Poppins:wght@600;700&family=Open+Sans:ital,wght@0,400;0,600;0,700;1,400&display=swap" rel="stylesheet">
<style>
  :root {
    --ink: #1f1f24;
    --muted: #444;
    --white: #ffffff;
    --royal: #1c3f94;
    --hero-bg: #5b5e67;
    --hero-dark: #4a4d55;
    --band: #e2eaf6;
    --frame: #d6d6d6;
    --tile-shade: rgba(60,60,60,.55);
  }
  * { box-sizing: border-box; margin: 0; padding: 0; }
  html, body { width: 1200px; height: 4488px; overflow: hidden; background: var(--white); }
  body { position: relative; font-family: "Open Sans", Arial, sans-serif; color: var(--ink); }
  .abs { position: absolute; }

  /* Hero */
  .hero { left: 0; top: 0; width: 1200px; height: 658px; background: linear-gradient(90deg, var(--hero-dark), var(--hero-bg) 55%, #62656e); overflow: hidden; }
  .hero-model { left: 560px; top: 0; width: 560px; height: 658px; background: radial-gradient(ellipse at 50% 55%, #c9cdd6 0%, #8d93a3 30%, #4f73b3 55%, rgba(91,94,103,0) 75%); }
  .brand { left: 110px; top: 68px; color: var(--white); font-family: "Poppins", sans-serif; font-weight: 600; font-size: 26px; display: flex; align-items: center; gap: 10px; }
  .brand .mark { width: 14px; height: 14px; border-radius: 50%; background: var(--white); }
  .nav { right: 113px; top: 34px; display: flex; gap: 36px; align-items: center; color: var(--white); font-weight: 700; font-size: 14px; letter-spacing: .5px; }
  .headline { left: 110px; top: 228px; color: var(--white); font-family: "Poppins", sans-serif; font-weight: 700; font-size: 50px; line-height: 70px; letter-spacing: -.5px; }
  .btn-shop { left: 111px; top: 387px; width: 127px; height: 45px; background: var(--royal); color: var(--white); font-weight: 700; font-size: 16px; display: flex; align-items: center; justify-content: center; letter-spacing: .5px; }
  .dots { left: 585px; top: 598px; display: flex; gap: 4px; }
  .dots span { width: 11px; height: 11px; border-radius: 50%; border: 1.5px solid var(--white); }
  .dots span:first-child { background: var(--white); }

  /* Intro */
  .intro { left: 250px; top: 762px; width: 700px; text-align: center; font-style: italic; font-size: 15px; line-height: 28px; color: var(--muted); }

  /* Section headings */
  .section-title { left: 0; width: 1200px; text-align: center; font-family: "Poppins", sans-serif; font-weight: 700; font-size: 44px; color: var(--ink); }
  .rule { left: 579px; width: 42px; height: 3px; background: var(--royal); }

  /* Collection tiles */
  .tile { display: flex; align-items: center; justify-content: center; color: var(--white); font-weight: 600; font-size: 35px; border: 1px solid var(--frame); }
  .tile-label { position: relative; }

  /* Products */
  .product-photo { border: 2px solid var(--frame); }
  .caption { text-align: center; font-size: 17px; line-height: 28px; color: var(--muted); }

  /* Newsletter */
  .newsletter { left: 0; top: 3730px; width: 1200px; height: 383px; background: var(--band); }
  .email { left: 261px; top: 3932px; width: 546px; height: 68px; background: var(--white); font-style: italic; font-size: 16px; color: #666; display: flex; align-items: center; padding-left: 20px; }
  .btn-subscribe { left: 807px; top: 3932px; width: 134px; height: 68px; background: #000; color: var(--white); font-weight: 700; font-size: 16px; display: flex; align-items: center; justify-content: center; }

  /* Footer */
  .footer-links { left: 110px; top: 4218px; list-style: none; font-size: 17px; line-height: 47px; color: var(--muted); }
  .social { left: 528px; top: 4206px; list-style: none; }
  .social li { display: flex; align-items: center; gap: 25px; height: 60px; font-size: 17px; color: var(--muted); }
  .social .dot { width: 48px; height: 48px; border-radius: 50%; border: 1.5px solid #555; }
  .copyright { right: 113px; top: 4218px; font-size: 17px; color: var(--muted); }
  .cards { right: 113px; top: 4272px; display: flex; gap: 8px; }
  .cards span { width: 44px; height: 30px; border-radius: 3px; display: flex; align-items: center; justify-content: center; font-size: 9px; font-weight: 600; color: var(--white); }
</style>
</head>
<body>

<header class="abs hero">
  <div class="abs hero-model" role="img" aria-label="Smiling young man in a white graphic tee against a grey wall"></div>
  <div class="abs brand"><span class="mark"></span>Forkora</div>
  <nav class="abs nav">
    <span>HOME</span><span>SHOP</span><span>ABOUT US</span>
    <svg width="18" height="18" viewBox="0 0 18 18"><circle cx="7.5" cy="7.5" r="5.5" fill="none" stroke="#fff" stroke-width="2"/><line x1="11.5" y1="11.5" x2="16" y2="16" stroke="#fff" stroke-width="2.5"/></svg>
    <svg width="18" height="18" viewBox="0 0 18 18"><path d="M1 2h3l2 9h9l2-7H5" fill="none" stroke="#fff" stroke-width="2"/><circle cx="7" cy="15" r="1.6" fill="#fff"/><circle cx="14" cy="15" r="1.6" fill="#fff"/></svg>
  </nav>
  <h1 class="abs headline">FIND YOUR YUM.<br>WEAR YOUR FOOD.</h1>
  <div class="abs btn-shop">SHOP NOW</div>
  <svg class="abs" style="left:110px;top:596px" width="26" height="16" viewBox="0 0 26 16"><path d="M2 8h23M8 2L2 8l6 6" fill="none" stroke="#fff" stroke-width="2.5"/></svg>
  <div class="abs dots"><span></span><span></span></div>
  <svg class="abs" style="left:1025px;top:597px" width="14" height="16" viewBox="0 0 14 16"><rect x="1" y="1" width="4" height="14" fill="#fff"/><rect x="9" y="1" width="4" height="14" fill="#fff"/></svg>
  <svg class="abs" style="left:1063px;top:596px" width="26" height="16" viewBox="0 0 26 16"><path d="M1 8h23M18 2l6 6-6 6" fill="none" stroke="#fff" stroke-width="2.5"/></svg>
</header>

<p class="abs intro">Forkora was born from the hearts of two foodies and travelholics based in Los Angeles and Chicago. Forkora is an expression of their mutual love of and wanderlust for all journey and let us help you find your yum!</p>

<h2 class="abs section-title" style="top:935px">Featured Collection</h2>
<div class="abs rule" style="top:1005px"></div>

<div class="abs tile" style="left:110px;top:1070px;width:477px;height:360px;background:linear-gradient(180deg,#4f7cc0,#3f6db4)" role="img" aria-label="Man wearing a blue graphic T-shirt"><span class="tile-label">T-Shirts</span></div>
<div class="abs tile" style="left:610px;top:1070px;width:479px;height:360px;background:linear-gradient(180deg,#6b6b6b,#303030 60%,#222)" role="img" aria-label="Woman wearing a black embroidered apron"><span class="tile-label">Apron</span></div>
<div class="abs tile" style="left:110px;top:1455px;width:310px;height:261px;background:linear-gradient(180deg,#7d7d7d,#6a6a6a)" role="img" aria-label="White mug with waffle print"><span class="tile-label">Cups</span></div>
<div class="abs tile" style="left:444px;top:1455px;width:310px;height:261px;background:linear-gradient(180deg,#777,#3a3a3a)" role="img" aria-label="Black ladies' tank top with gelato print"><span class="tile-label">Ladie’s Tank</span></div>
<div class="abs tile" style="left:779px;top:1455px;width:310px;height:261px;background:linear-gradient(180deg,#777,#2a2a2a)" role="img" aria-label="Man in a black hooded sweatshirt"><span class="tile-label">Sweatshirt</span></div>

<h2 class="abs section-title" style="top:1815px">Featured Products</h2>
<div class="abs rule" style="top:1884px"></div>

<div class="abs product-photo" style="left:110px;top:1956px;width:590px;height:702px;background:radial-gradient(ellipse at 50% 55%,#1a1a1a 0%,#222 35%,#e6e6e6 60%,#fff 80%)" role="img" aria-label="Man wearing a black unisex T-shirt with orange print"></div>
<div class="abs product-photo" style="left:725px;top:1956px;width:365px;height:300px;background:radial-gradient(ellipse at 50% 50%,#c9c9cc 0%,#bbb 30%,#fff 60%)" role="img" aria-label="Man wearing a heather grey unisex T-shirt"></div>
<p class="abs caption" style="left:725px;top:2256px;width:365px">Whisk Me Away Tonight<br>- Unisex T-Shirt<br>from $22</p>
<div class="abs product-photo" style="left:725px;top:2359px;width:365px;height:299px;background:radial-gradient(ellipse at 50% 50%,#a9a9a9 0%,#a0a0a0 35%,#fff 62%)" role="img" aria-label="Grey ladies' scoopneck T-shirt"></div>
<p class="abs caption" style="left:236px;top:2691px;width:340px">Whisk Me Away Tonight<br>- Unisex T-Shirt<br>from $25</p>
<p class="abs caption" style="left:725px;top:2691px;width:365px">Whisk Me Away Tonight -<br>Ladies' Scoopneck T-Shirt<br>from $30</p>

<div class="abs product-photo" style="left:110px;top:2840px;width:364px;height:282px;background:radial-gradient(ellipse at 50% 50%,#f2f2f2 0%,#eee 40%,#fff 65%)" role="img" aria-label="White unisex T-shirt with waffle print"></div>
<p class="abs caption" style="left:110px;top:3130px;width:364px">Waffles Beat Pancakes -<br>Unisex T-Shirt<br>from $25</p>
<div class="abs product-photo" style="left:110px;top:3214px;width:364px;height:280px;background:radial-gradient(ellipse at 50% 55%,#333 0%,#2c2c2c 30%,#fff 58%)" role="img" aria-label="Black ladies' tank top with gelato print"></div>
<p class="abs caption" style="left:110px;top:3531px;width:364px">Love at First Gelato<br>- Ladies' Tank Regular<br>price $25</p>
<div class="abs product-photo" style="left:500px;top:2840px;width:590px;height:658px;background:radial-gradient(ellipse at 50% 60%,#111 0%,#1a1a1a 35%,#e8e8e8 62%,#fff 80%)" role="img" aria-label="Woman wearing a black embroidered apron"></div>
<p class="abs caption" style="left:500px;top:3531px;width:590px">Whisk Me Away Tonight<br>Embroidered Apron Regular<br>price $35</p>

<section class="abs newsletter"></section>
<h2 class="abs section-title" style="top:3808px">Subscribe to our Newsletter</h2>
<div class="abs rule" style="top:3876px"></div>
<div class="abs email">Your Email</div>
<div class="abs btn-subscribe">SUBSCRIBE</div>

<ul class="abs footer-links">
  <li>About Us</li>
  <li>Blog: The Fork Chronicles</li>
  <li>Contact</li>
  <li>Privacy Policy</li>
  <li>Return Policy</li>
</ul>
<ul class="abs social">
  <li><span class="dot"></span>Pinwheel</li>
  <li><span class="dot"></span>Chirper</li>
  <li><span class="dot"></span>Lenslog</li>
  <li><span class="dot"></span>Orbit Plus</li>
</ul>
<p class="abs copyright">© 2019, Forkora</p>
<div class="abs cards">
  <span style="background:#c94a2a">Tally</span>
  <span style="background:#2a3f8f">Norra</span>
  <span style="background:#3b73b9">Bexa</span>
  <span style="background:#e07a28">Crest</span>
</div>

</body>
</html>
```